FieldNest.com FACELIFT design for the online store

A) GENERAL
We need a small FACELIFT design with a short styleguide for our online store http://FieldNest.com (online store for sport goods; the store is just now in responsive design; actually only in German). The store is the first online store worldwide with 3d images for all products.
B) Designers: PLEASE NOTE:
- We don't want change functionality!
- We only want a small facelift.
- We don't need a fully coded website.
C) We only need for the responsive design views:
1. the home page design (one page)
http://www.fieldnest.com/de/
2. the category listing design (one page)
http://www.fieldnest.com/de/alle/running.html
3. the product detail page (one page)
http://www.fieldnest.com/de/varnok-tz-max-3d-qrt-herren-traillaufschuhe-dura-flex.html
4. the cms page (textonly !!!)
http://www.fieldnest.com/de/versand-und-lieferung
5. the Mega drop down
D) We intend to change/use:
- maybe to use a background image in the start page, and each category
- change the header
- change the font sizes for the titles (maybe in capital letters)
- change the mega drop down

```html
<!DOCTYPE html>
<html lang="en">
<head>
<meta charset="utf-8">
<title>FieldNest.com – Home</title>
<link rel="stylesheet" href="https://fonts.googleapis.com/css2?family=Raleway:wght@400;500;600;700&family=Roboto:wght@400;500;700&display=swap">
<style>
:root{
  --pink:#e0127f;
  --orange:#ec6a0c;
  --black:#0b0b0b;
  --footer:#0d0d0d;
  --footer-bottom:#070707;
  --ink:#1a1a1a;
  --line:#d9d9d9;
  --white:#fff;
}
*{margin:0;padding:0;box-sizing:border-box}
html,body{width:743px;height:1200px;overflow:hidden;background:var(--white)}
body{position:relative;font-family:"Raleway",sans-serif;color:var(--ink)}
.abs{position:absolute}

/* header */
.site-header{position:absolute;left:0;top:0;width:743px;height:58px;background:var(--white)}
.logo{left:118px;top:20px;font-weight:700;font-size:19px;letter-spacing:1px;color:var(--black)}
.header-divider{left:327px;top:6px;width:1px;height:46px;background:#e6e6e6}
.top-links{right:121px;top:9px;font-size:7.5px;font-weight:600;color:#333;letter-spacing:.2px;white-space:nowrap}
.top-links span{margin:0 4px;color:#999}
.cart{right:121px;top:31px;display:flex;align-items:center;gap:5px}
.cart-text{font-size:5.5px;color:#555;line-height:1.1}
.cart-text b{display:block;color:var(--pink);font-size:8.5px;font-weight:600}

/* hero */
.hero-band{left:0;top:58px;width:743px;height:270px;
  background:
   linear-gradient(90deg,#2e2e2e 0%,#6a6a6a 8%,#3c3c3c 16%,rgba(0,0,0,0) 16%,rgba(0,0,0,0) 84%,#4a4a4a 84%,#8c8c8c 92%,#353535 100%),
   #444}
.main-nav{left:118px;top:58px;width:508px;height:28px;background:var(--black);display:flex}
.main-nav a{flex:1 1 auto;display:flex;align-items:center;justify-content:center;color:var(--white);text-decoration:none;font-size:8.4px;font-weight:500;border-right:1px solid #333;letter-spacing:.2px}
.main-nav a:last-child{border-right:0}
.hero-photo{left:118px;top:86px;width:508px;height:242px;
  background:
   linear-gradient(200deg,rgba(0,0,0,0) 55%,#9c8f7f 55%,#d3cbbd 70%,#8a7d6c 100%),
   linear-gradient(172deg,rgba(0,0,0,0) 62%,#c4c2c6 62%,#a9a5a8 72%,rgba(0,0,0,0) 72%),
   linear-gradient(180deg,#2a48c2 0%,#4d75d9 35%,#8fb0e8 62%,#c3cde0 75%)}
.hero-caption{left:160px;top:152px;width:223px;height:98px;background:var(--pink);padding:15px 15px 0;color:var(--white)}
.hero-caption h1{font-family:"Roboto",sans-serif;font-weight:500;font-size:16.5px;line-height:1.1;text-transform:uppercase;white-space:nowrap}
.hero-caption h1 strong{display:block;font-size:20.5px;font-weight:500;margin-top:2px}
.hero-caption p{font-size:6.2px;line-height:1.55;margin-top:4px}
.hero-arrow{top:184px}

/* tiles */
.tile{top:350px;width:166px;height:126px;overflow:hidden}
.tile-photo{position:absolute;inset:0}
.tile-band{position:absolute;left:0;bottom:0;width:100%;height:34px;background:rgba(0,0,0,.78);color:var(--white);text-align:center;padding-top:7px}
.tile-band.pink{background:rgba(224,18,127,.92)}
.tile-band h3{font-size:9.5px;font-weight:500;text-transform:uppercase}
.tile-band p{font-size:6px;margin-top:2px}

/* about */
.about{left:0;top:456px;width:743px;height:250px;background:radial-gradient(ellipse at center,#fafafa 40%,#e6e6e6 100%)}
.about-title{left:119px;top:528px;font-size:18px;font-weight:400;color:#111}
.about-text{left:119px;width:277px;font-size:5.8px;line-height:1.6;color:#333}
.btn-orange{left:118px;top:622px;width:60px;height:17px;background:var(--orange);color:var(--white);font-size:6.4px;font-weight:600;display:flex;align-items:center;justify-content:center;border-radius:2px;letter-spacing:.3px}
.about-bike{left:412px;top:504px;width:198px;height:166px;border-radius:6px;
  background:linear-gradient(160deg,#3f6f93 0%,#2d3a44 40%,#d36a24 55%,#1d1f22 70%,#4a4f55 100%)}

/* products */
.section-title{left:0;width:743px;top:734px;text-align:center;font-family:"Roboto",sans-serif;font-weight:400;font-size:13.5px;color:var(--pink)}
.product{top:766px;width:123px;height:151px;border:1px solid var(--line);background:var(--white)}
.product-img{position:absolute;left:24px;top:10px;width:75px;height:66px;border-radius:6px}
.product-name{position:absolute;left:11px;top:94px;font-size:8px;color:#111}
.product-desc{position:absolute;left:11px;top:107px;font-size:5.6px;color:#555;white-space:nowrap}
.product-foot{position:absolute;left:0;bottom:0;width:100%;height:28px;border-top:1px solid var(--line);background:#f7f7f7}
.price{position:absolute;left:12px;top:9px;font-family:"Roboto",sans-serif;font-size:9px;color:var(--pink)}
.btn-cart{position:absolute;right:11px;top:5px;width:48px;height:14px;background:#111;color:var(--white);font-size:5.6px;display:flex;align-items:center;justify-content:center;border-radius:1px}

/* brands */
.brands{left:0;top:956px;width:743px;height:51px;background:#f4f4f4;border-top:1px solid #ddd;display:flex;align-items:center;justify-content:center}
.brand{width:63.5px;text-align:center;font-weight:700;font-size:10.5px;color:#222;text-transform:uppercase;letter-spacing:.4px}

/* footer */
.site-footer{left:0;top:1007px;width:743px;height:158px;background:var(--footer)}
.foot-col{top:1040px;color:#8a8a8a;font-size:6.2px}
.foot-col h4{color:var(--white);font-size:9px;font-weight:500;text-transform:uppercase;margin-bottom:5px;letter-spacing:.2px}
.foot-col li{list-style:none;line-height:13px}
.email-field{left:417px;top:1071px;width:138px;height:17px;background:var(--white);font-size:5.5px;color:#777;padding:5px 7px}
.btn-subscribe{left:417px;top:1093px;width:59px;height:17px;background:var(--pink);color:var(--white);font-size:7px;display:flex;align-items:center;justify-content:center}
.badge{top:1121px;width:26px;height:26px;border-radius:50%;background:#7b6a38;border:2px solid #b89b45}
.badge.blue{background:#2c3f74;border-color:#5567a0}
.footer-bottom{left:0;top:1165px;width:743px;height:35px;background:var(--footer-bottom)}
.copyright{left:117px;top:1179px;font-size:5.6px;color:#555}
.social{top:1176px;width:10px;height:10px;border-radius:2px;background:#d8d8d8}
</style>
</head>
<body>

<header class="site-header">
  <div class="abs logo">FIELDNEST.COM</div>
  <div class="abs header-divider"></div>
  <nav class="abs top-links">SIGN IN<span>|</span>LOGIN<span>|</span>FREE SHIPPING</nav>
  <div class="abs cart">
    <svg width="16" height="13" viewBox="0 0 16 13" aria-hidden="true"><path d="M1 1h3l2 7h7l2-5H5" fill="none" stroke="#e0127f" stroke-width="1.4"/><circle cx="7" cy="11" r="1.2" fill="#e0127f"/><circle cx="12" cy="11" r="1.2" fill="#e0127f"/></svg>
    <div class="cart-text">My Cart<b>0 items</b></div>
  </div>
</header>

<div class="abs hero-band" role="img" aria-label="Black and white photos of a runner and a climber behind the hero"></div>
<nav class="abs main-nav">
  <a>HOME</a><a>MEN'S</a><a>WOMEN'S</a><a>CHILDREN</a><a>YOUTH</a><a>GIFT IDEAS</a><a>SUPPORT</a>
</nav>
<div class="abs hero-photo" role="img" aria-label="Mountain biker riding over rocky alpine terrain under a blue sky"></div>
<div class="abs hero-caption">
  <h1>Sports Addition<strong>Bike Oster Action</strong></h1>
  <p>In massa libero interdum nec interdum vel blandit sed nulla In ullamcorper est eget tempor cursus neque mi</p>
</div>
<svg class="abs hero-arrow" style="left:127px" width="16" height="26" viewBox="0 0 16 26" aria-hidden="true"><path d="M13 2 3 13l10 11" fill="none" stroke="#111" stroke-width="3"/></svg>
<svg class="abs hero-arrow" style="left:596px" width="16" height="26" viewBox="0 0 16 26" aria-hidden="true"><path d="M3 2l10 11L3 24" fill="none" stroke="#111" stroke-width="3"/></svg>

<section class="abs about" aria-hidden="true"></section>

<article class="abs tile" style="left:118px">
  <div class="tile-photo" role="img" aria-label="Running shoe on sunlit grass" style="background:linear-gradient(180deg,#f6e3a0 0%,#e8b94c 35%,#a9952e 60%,#4f6b1e 100%)"></div>
  <div class="tile-band"><h3>Why Our Products</h3><p>Mauris vel lacus vitae felis vestibulum</p></div>
</article>
<article class="abs tile" style="left:289px">
  <div class="tile-photo" role="img" aria-label="Two hikers on a mountain trail" style="background:linear-gradient(180deg,#3f74d0 0%,#86aee0 28%,#b9b8b0 45%,#6f7f55 70%,#4d5a3a 100%)"></div>
  <div class="tile-band pink"><h3>Special Deals</h3><p>Mauris vel lacus vitae felis vestibulum</p></div>
</article>
<article class="abs tile" style="left:460px">
  <div class="tile-photo" role="img" aria-label="Two cyclists in helmets cheering" style="background:linear-gradient(180deg,#5c93dc 0%,#9cbbe6 30%,#d8d8dc 45%,#8a6a55 62%,#2a2a2a 100%)"></div>
  <div class="tile-band"><h3>Order Now</h3><p>Mauris vel lacus vitae felis vestibulum</p></div>
</article>

<h2 class="abs about-title">About Our Company</h2>
<p class="abs about-text" style="top:557px">Mauris vel lacus vitae felis vestibulum volutpat Etiam est nunc venenatis in tristique eu imperdiet ac nisl Cum sociis natoque penatibus et magnis dis parturient montes nascetur ridiculus mus In iaculis facilisis massa Etiam eu urna Sed porta Suspendisse quam leo</p>
<p class="abs about-text" style="top:590px">In massa libero interdum nec interdum vel blandit sed nulla In ullamcorper est eget tempor cursus neque mi consectetuer mi a ultricies massa est sed nisl Class aptent ta</p>
<div class="abs btn-orange">READ MORE</div>
<div class="abs about-bike" role="img" aria-label="Full suspension mountain bike in blue and orange"></div>

<h2 class="abs section-title">TOP SELLING PRODUCTS</h2>

<article class="abs product" style="left:118px">
  <div class="product-img" role="img" aria-label="Red and orange mountaineering boot" style="background:linear-gradient(150deg,#f0a02a,#d8381a 50%,#2a2a2a)"></div>
  <div class="product-name">Product Name</div>
  <div class="product-desc">Morbi diam mauris viverra in gravid</div>
  <div class="product-foot"><span class="price">£57.58</span><span class="btn-cart">Add to Cart</span></div>
</article>
<article class="abs product" style="left:247px">
  <div class="product-img" role="img" aria-label="Mint green running shoe" style="background:linear-gradient(150deg,#bfe8e2,#6fc2b7 55%,#3a4a48)"></div>
  <div class="product-name">Product Name</div>
  <div class="product-desc">Morbi diam mauris viverra in gravid</div>
  <div class="product-foot"><span class="price">£57.58</span><span class="btn-cart">Add to Cart</span></div>
</article>
<article class="abs product" style="left:376px">
  <div class="product-img" role="img" aria-label="Grey climbing belay device" style="background:linear-gradient(150deg,#e0e0e0,#9c9c9c 55%,#5e5e5e)"></div>
  <div class="product-name">Product Name</div>
  <div class="product-desc">Morbi diam mauris viverra in gravid</div>
  <div class="product-foot"><span class="price">£87.58</span><span class="btn-cart">Add to Cart</span></div>
</article>
<article class="abs product" style="left:505px">
  <div class="product-img" role="img" aria-label="Black and lime mountain bike" style="background:linear-gradient(150deg,#c9dd3a,#5a6a22 45%,#1c1c1c)"></div>
  <div class="product-name">Product Name</div>
  <div class="product-desc">Morbi diam mauris viverra in gravid</div>
  <div class="product-foot"><span class="price">£62.58</span><span class="btn-cart">Add to Cart</span></div>
</article>

<section class="abs brands" aria-label="Brands">
  <span class="brand">Alvero</span><span class="brand">Dynara</span><span class="brand">Tridon</span><span class="brand">Hallwyn</span><span class="brand">Pokel</span><span class="brand">Atomra</span><span class="brand">Kestra</span><span class="brand">Garvik</span>
</section>

<footer class="abs site-footer"></footer>
<div class="abs foot-col" style="left:117px"><h4>Company</h4><ul><li>About FieldNest.com</li><li>Our stores Overview</li><li>Jobs</li><li>Terms and Conditions</li><li>Site Map</li></ul></div>
<div class="abs foot-col" style="left:217px"><h4>Products</h4><ul><li>Shipping and Delivery</li><li>Payment Methods</li><li>Return</li><li>Service</li><li>Help</li></ul></div>
<div class="abs foot-col" style="left:325px"><h4>Support</h4><ul><li>FAQs</li><li>Privacy Policy</li><li>Recommendations</li><li>Contact</li></ul></div>
<div class="abs foot-col" style="left:417px"><h4>Newsletter Sign Up</h4><ul><li>Please sign up here for latest deals</li></ul></div>
<div class="abs email-field">Email address</div>
<div class="abs btn-subscribe">SUBSCRIBE</div>
<div class="abs badge blue" style="left:416px"></div>
<div class="abs badge blue" style="left:449px"></div>
<div class="abs badge" style="left:481px"></div>

<div class="abs footer-bottom"></div>
<div class="abs copyright">© 2015 Company Name All right reserved Term of Use</div>
<span class="abs social" style="left:578px"></span>
<span class="abs social" style="left:592px"></span>
<span class="abs social" style="left:606px"></span>

</body>
</html>
```